A unique communication angle to crowdfunding

Looking for a fresh redesign of a crowd funding website that deals in real estate. I already have the content, but am looking to take the design to the next level.

Existing real estate crowd funding sites focus on the real estate. I want to explore communication angle that:
- puts the investor in the centre of the communication: "become a baron"
- highlights the international nature (international properties, international investors)

There's also quite a lot of copy on the site, as we need to explain the service in quite a bit of detail. There's room to reduce the copy and replace with graphics. Could also consider clicking to see different text (see our difference section in http://galleonfairs.com)

The backend of the platform is already being worked on by a specialist crowd funding service provider.

In total there are 5 pages to be designed.

The homepage is really important. Right now it looks quite dated. It doesn't have a great layout. Note there is no mobile version of the website, so the pages need to be seen well on mobile devices. When looking at the brief, refer to the following links too:

current website:
http://pennyduke.com

some revisions made so far:
http://preview.stakeharbor.com/7K3LQ9

Attached are logo files and another file which contained copy for the pages. No need to rework the logo.

Please make sure to use the same copy in the brief on the webpages, to ensure the layouts work. Designers are free to propose images they feel work on the pages.

I would like to see if rather than tweaking the pages, it's possible to come up with a better design concept. If the 5 pages are accepted, there's a chance I'll request an additional 4 pages.
Updates

Please note the font used in the logo is called "harabara" in case you decide to use it in any of the titles, etc.

Please note there is one additional page for which we would like to review designs. Note the page would be a template to be used on all future real estate detail pages. Here is an example of the current design for reference:

http://pennyduke.com/projects/view/14

In total there are 5 page designs required, (homepage + 4)

Thank you

FYI -

Just a quick note to give information from similar UK real estate crowdfunding sites:
http://www.housewalrus.co.uk
http://tiderock.co.uk
https://www.fundquarry.com

Of the above, only tiderock has a nice clean looking landing page. Information is clear and well laid out.

Hi all, just uploaded a new file in the brief. Contains some comments and a website reference. I thought it may help to explain how we could convey international aspect as well as how we could convey images in a more modern way. This is an option you can consider, but its entirely up to you how how answer the brief. Thanks!

Reason: As requested by some designers needing more time to complete their work. Continue to share your work in progress and receive timely feedback before the deadline.

We would like to let you know that we have just shortlisted the best designs. Together with that, we have also passed some detailed feedback to all designers who weren't shortlisted. If we didn't contact you, please let us know. If you haven't submitted a design or are working on revisions, please note these will no longer be taken into account now. We hope you understand that we need to close the project today. Thank you all once again for your great work and design concepts. Here's hoping we meet again on a future design brief. Cheers, pennyduke team.

Target Market(s)

At the moment, only rich are able to buy real estate. With this service, anyone can become a landlord. Target buyers:

Young professionals, looking to diversify from stock market and lower risk
People nearing retirement, looking for stable rental incomes
Retirees - looking to supplement pensions with possibility of capital gains
Parents - looking for a way to save long term for their children (instead of low interest paying bank accounts)

Industry/Entity Type

Communication

Font styles to use
Sans Serif
Other font styles liked:
• harabara

Colors
add136
f5f9eb
959595
000000

Requirements
Must have
• Overall, the site must convey "whoever you are, you too can become a landlord", and that you don't need to be wealthy to invest in real estate. See

Communication should put the investor (or the baron) at the centre. The investor can be any of those described in the target market.

Show the aspirational side of property ownership.

In addition to the investor/baron character, the second main theme is international. No other real estate crowdfunding website highlights this.
Nice to have
• Banner could show different consumer types, to illustrate that the service can appeal to many different profiles. Refer to attached file "home page reference - plainasbread.com" as an example of how this could be done.

Aim to show the international side of the service. Properties around the world, investors around the world.

```html
<!DOCTYPE html>
<html lang="en">
<head>
<meta charset="utf-8">
<title>pennyduke – Become an international property landlord</title>
<link href="https://fonts.googleapis.com/css2?family=Open+Sans:wght@400;600;700&display=swap" rel="stylesheet">
<style>
:root{
  --green:#add136;
  --green-dark:#8fb321;
  --green-pale:#f5f9eb;
  --grey:#959595;
  --grey-light:#ececec;
  --grey-mid:#d6d6d6;
  --grey-dark:#555555;
  --ink:#000000;
  --text:#333333;
  --white:#ffffff;
}
*{box-sizing:border-box;margin:0;padding:0}
html,body{width:1200px;height:2313px;overflow:hidden}
body{background:linear-gradient(#f4f4f4,#e4e4e4);font-family:"Open Sans",Arial,sans-serif;color:var(--text);font-size:13px;position:relative}
.page{position:absolute;left:130px;top:0;width:940px;height:2213px;background:var(--white);box-shadow:0 0 14px rgba(0,0,0,.12)}

/* header */
.site-header{height:92px;position:relative}
.brand{position:absolute;left:35px;top:8px;display:flex;align-items:center;gap:10px}
.brand-dot{width:38px;height:38px;border-radius:50%;background:var(--green)}
.brand-name{font-size:28px;font-weight:700;color:var(--green)}
.utility{position:absolute;right:35px;top:10px;display:flex;gap:8px}
.lang{width:110px;height:22px;border:1px solid var(--grey-mid);font-size:11px;padding:2px 6px;display:flex;justify-content:space-between;align-items:center}
.search-field{width:230px;height:22px;border:1px solid var(--grey-mid)}
.search-btn{height:22px;padding:0 16px;background:var(--green);color:var(--white);font-size:11px;font-weight:600;line-height:22px}
.main-nav{position:absolute;right:35px;top:52px;display:flex;font-size:14px;color:var(--ink)}
.main-nav a{color:inherit;text-decoration:none;padding:0 12px;border-left:1px solid var(--grey-mid)}
.main-nav a:first-child{border-left:none}

/* slider */
.hero{height:318px;position:relative}
.hero-frame{position:absolute;left:35px;right:35px;top:0;height:282px;border:6px solid #3a3a3a;overflow:hidden}
.hero-photo{position:absolute;inset:0;background:linear-gradient(160deg,#c9d6e0 0%,#a7b3a2 45%,#6e6a5c 75%,#3f3d36 100%)}
.hero-caption{position:absolute;left:0;right:0;bottom:0;padding:10px 40px 12px;background:rgba(0,0,0,.45);color:var(--white)}
.hero-caption h1{font-size:20px;font-weight:400;letter-spacing:.3px;white-space:nowrap}
.hero-caption p{font-size:12.5px;white-space:nowrap}
.hero-arrow{position:absolute;top:110px;width:26px;height:40px;background:rgba(0,0,0,.5)}
.hero-arrow.prev{left:0}.hero-arrow.next{right:0}
.hero-dots{position:absolute;left:50%;top:294px;transform:translateX(-50%);display:flex;gap:5px}
.hero-dots span{width:14px;height:8px;background:var(--grey-mid)}
.hero-dots span.on{background:var(--green)}

/* find */
.find{margin:14px 35px 0;height:160px;background:#f1f1f1;border:1px solid #e2e2e2;display:flex;gap:22px;padding:18px 22px}
.find-card{flex:1;position:relative;display:flex;gap:10px}
.find-icon{width:112px;height:100px;background:linear-gradient(#fafafa,#e3e3e3);display:flex;align-items:center;justify-content:center}
.find-body{flex:1;background:var(--white);padding:12px 14px;height:100px;border:1px solid #e6e6e6}
.find-body h2{color:var(--green);font-size:16px;font-weight:700;margin-bottom:4px}
.find-body p{font-size:11.5px;line-height:1.4}
.pill{position:absolute;right:0;bottom:-4px;background:var(--green);color:var(--white);font-size:11px;padding:4px 14px;border-radius:12px}

/* intro + chart */
.intro{height:190px;margin:14px 35px 0;display:flex;gap:30px}
.intro-copy{flex:1;font-size:12.5px;line-height:1.55}
.intro-copy h3{color:var(--green);font-size:15px;margin:10px 0 6px}
.intro-copy p{margin-bottom:9px}
.intro-copy a{color:var(--green);text-decoration:none}
.stats{width:300px;position:relative}
.stats-note{font-size:9.5px;color:var(--grey);line-height:1.3;margin-bottom:4px}
.stats svg{position:absolute;left:0;top:30px}
.legend{position:absolute;left:170px;top:88px;font-size:12px;line-height:1.9}
.legend i{display:inline-block;width:10px;height:10px;margin-right:5px;vertical-align:-1px}

/* pillars */
.pillars{height:232px;margin:10px 35px 0;display:flex;gap:34px}
.pillar{flex:1;background:linear-gradient(#f3f3f3,#dcdcdc);border:1px solid #d0d0d0;display:flex;flex-direction:column}
.pillar h2{text-align:center;font-size:20px;font-weight:700;color:#444;padding-top:12px;height:48px}
.pillar-icon{flex:1;display:flex;align-items:center;justify-content:center}
.pillar-foot{height:72px;background:var(--green);color:var(--white);font-size:13px;font-weight:600;text-align:center;padding:14px 30px;line-height:1.4}

/* featured */
.featured{height:452px;margin:14px 35px 0;background:#f4f4f4;border:1px solid #e4e4e4;padding:14px 24px}
.section-title{text-align:center;color:var(--green);font-size:20px;font-weight:700}
.section-sub{text-align:center;font-size:11.5px;color:#555;margin:4px auto 16px;width:360px;line-height:1.4}
.projects{display:flex;gap:26px}
.project{flex:1;background:var(--white);border:1px solid #dcdcdc}
.project-photo{height:150px;position:relative;background:linear-gradient(#9fb0c2,#6f7a86 60%,#4a5058)}
.project-photo.p2{background:linear-gradient(#b8c6d4,#7d8a96 55%,#3f454c)}
.project-photo.p3{background:linear-gradient(#5a6470,#2f353c 60%,#1c1f24)}
.price{position:absolute;right:0;top:8px;background:var(--green);color:var(--white);font-size:11px;font-weight:700;padding:4px 10px}
.project-body{padding:10px 10px 0;height:126px}
.project-body h3{color:var(--green);font-size:12.5px;font-weight:700}
.project-body p{font-size:10.5px;line-height:1.35;color:#555;margin:4px 0 10px}
.bar{height:12px;border:1px solid var(--grey-mid);background:var(--white)}
.bar span{display:block;height:100%;background:var(--green)}
.funded{font-size:10.5px;color:#555;margin-top:3px}
.project-btn{height:44px;background:var(--green);color:var(--white);font-size:14px;font-weight:600;padding:12px 12px}

/* press */
.press{height:108px;margin:12px 35px 0;border:1px solid #e0e0e0;padding:10px 22px}
.press h4{font-size:9px;color:var(--grey);font-weight:600;margin-bottom:8px}
.press-row{display:flex;gap:20px;align-items:center;margin-bottom:8px}
.badge{height:22px;background:#bdbdbd}

/* community */
.community{height:110px;margin:12px 35px 0;background:var(--green-pale);border:1px solid #e3ebcc;padding:12px 30px;text-align:center}
.community h2{color:var(--green);font-size:17px;font-weight:700}
.community p.lead{font-size:12px;font-weight:600;color:#444;margin:2px 0 10px}
.community ul{list-style:none;display:flex;justify-content:space-around}
.community li{color:var(--green);font-size:11.5px;width:200px;line-height:1.35}

/* legal */
.legal{height:400px;margin:12px 35px 0;border:1px solid #e0e0e0;padding:34px 40px;font-size:12px;color:#555;line-height:1.8;font-style:italic}
.legal p+p{margin-top:50px}

/* footer */
.site-footer{position:absolute;left:0;right:0;top:2213px;height:100px;background:var(--grey-dark);color:var(--white);text-align:center;font-size:11px}
.foot-nav{display:flex;justify-content:center;gap:34px;padding-top:14px}
.follow{display:flex;justify-content:center;align-items:center;gap:6px;margin-top:14px;font-size:13px;font-weight:600;letter-spacing:1px}
.follow i{width:20px;height:20px;background:#8a8a8a;display:inline-block}
.copyright{margin-top:10px}
</style>
</head>
<body>
<div class="page">
  <header class="site-header">
    <div class="brand"><span class="brand-dot"></span><span class="brand-name">pennyduke</span></div>
    <div class="utility">
      <div class="lang">English <span>▾</span></div>
      <div class="search-field"></div>
      <div class="search-btn">Search</div>
    </div>
    <nav class="main-nav">
      <a href="#">Home</a><a href="#">About Us</a><a href="#">How it Works</a><a href="#">Discover A Project</a><a href="#">Blog</a><a href="#">Testimonials</a><a href="#">Contact Us</a>
    </nav>
  </header>

  <section class="hero">
    <div class="hero-frame">
      <div class="hero-photo" role="img" aria-label="Modern apartment building with balconies under a clear sky"></div>
      <div class="hero-arrow prev"><svg width="26" height="40"><path d="M16 12 L9 20 L16 28" stroke="#fff" stroke-width="3" fill="none"/></svg></div>
      <div class="hero-arrow next"><svg width="26" height="40"><path d="M10 12 L17 20 L10 28" stroke="#fff" stroke-width="3" fill="none"/></svg></div>
      <div class="hero-caption">
        <h1>LOREM IPSUM DOLOR SIT AMET, CONSECTETEUR ADIPISCING ELIT</h1>
        <p>Lorem ipsum dolor sit amet, consectetuer adipiscing elit. Sed diam nonummy nibh euismod tincidunt ut laoreet.</p>
      </div>
    </div>
    <div class="hero-dots"><span class="on"></span><span></span><span></span></div>
  </section>

  <section class="find">
    <div class="find-card">
      <div class="find-icon"><svg width="60" height="60" viewBox="0 0 60 60"><path d="M30 8 V50 M12 18 H48 M18 50 H42" stroke="#7a7a7a" stroke-width="4" fill="none"/><path d="M12 18 L5 34 H19 Z M48 18 L41 34 H55 Z" fill="var(--green)"/></svg></div>
      <div class="find-body"><h2>FIND PROPERTIES</h2><p>Sign up to browse the portfolio your journey to becoming a real estate baron starts here.</p></div>
      <span class="pill">Become A Member</span>
    </div>
    <div class="find-card">
      <div class="find-icon"><svg width="60" height="60" viewBox="0 0 60 60"><path d="M10 30 L30 12 L50 30 V50 H10 Z" fill="#7a7a7a"/><circle cx="30" cy="36" r="8" fill="var(--green)"/></svg></div>
      <div class="find-body"><h2>FIND BUYERS</h2><p>Submit property or development and raise funds from our real estate barons.</p></div>
      <span class="pill">Submit a Project</span>
    </div>
  </section>

  <section class="intro">
    <div class="intro-copy">
      <p>With pennyduke, become an international property landlord.</p>
      <h3>Together we can buy</h3>
      <p>Members in the community can participate in a variety of land and property projects. Choose property and diversify across growing cities arround the world.</p>
      <p>start with as little as 1% in project and plan your steps to becoming a true baron. Visit <a href="#">how it works</a> to find out more.</p>
    </div>
    <div class="stats">
      <p class="stats-note">* Graphic shows the combined USD$ amount invested in projects and pledged from members across pennyduke.</p>
      <svg width="160" height="160" viewBox="0 0 160 160">
        <circle cx="80" cy="80" r="58" fill="none" stroke="var(--green)" stroke-width="34"/>
        <circle cx="80" cy="80" r="58" fill="none" stroke="#d8e8a8" stroke-width="34" stroke-dasharray="58.3 364.4" transform="rotate(-90 80 80)"/>
        <text x="80" y="76" text-anchor="middle" font-size="14" fill="#333" font-family="Open Sans, sans-serif">USD</text>
        <text x="80" y="96" text-anchor="middle" font-size="18" font-weight="700" fill="#333" font-family="Open Sans, sans-serif">$2.6m</text>
      </svg>
      <div class="legend"><div><i style="background:var(--green)"></i>Pledged 84%</div><div><i style="background:#d8e8a8"></i>Invested 16%</div></div>
    </div>
  </section>

  <section class="pillars">
    <div class="pillar"><h2>Simple</h2>
      <div class="pillar-icon"><svg width="90" height="90" viewBox="0 0 90 90"><circle cx="45" cy="45" r="40" fill="var(--green)"/><path d="M25 46 L45 28 L65 46 V64 H25 Z" fill="#fff"/></svg></div>
      <div class="pillar-foot">Browse project, like booking a hotel online</div></div>
    <div class="pillar"><h2>Transparent</h2>
      <div class="pillar-icon"><svg width="90" height="90" viewBox="0 0 90 90"><circle cx="45" cy="45" r="40" fill="var(--green)"/><path d="M45 22 V66 M26 32 H64 M33 66 H57" stroke="#fff" stroke-width="4" fill="none"/><path d="M26 32 L20 48 H32 Z M64 32 L58 48 H70 Z" fill="#fff"/></svg></div>
      <div class="pillar-foot">100% of profit shared among the community</div></div>
    <div class="pillar"><h2>Collaborative</h2>
      <div class="pillar-icon"><svg width="90" height="90" viewBox="0 0 90 90"><circle cx="45" cy="45" r="40" fill="var(--green)"/><path d="M30 44 L45 30 L60 44 V60 H30 Z" fill="#fff"/><circle cx="45" cy="50" r="5" fill="var(--green)"/></svg></div>
      <div class="pillar-foot">Shares the purchase costs and share the benefits</div></div>
  </section>

  <section class="featured">
    <h2 class="section-title">Fetured Projects</h2>
    <p class="section-sub">Brief details of new and popular projects. To view full listings, you will be required to sign up and become a member</p>
    <div class="projects">
      <article class="project">
        <div class="project-photo" role="img" aria-label="City skyline with high-rise towers"><span class="price">From GBP 3,800</span></div>
        <div class="project-body"><h3>Lorem ipsum dolor sit amet</h3><p>Lorem ipsum dolor sit amet, consectetuer adipiscing elit. Sed diam nonummy nibh euismod tincidunt.</p><div class="bar"><span style="width:5%"></span></div><div class="funded">5% funded</div></div>
        <div class="project-btn">See Project Details</div>
      </article>
      <article class="project">
        <div class="project-photo p2" role="img" aria-label="Downtown office towers seen from street level"><span class="price">From GBP 1,276</span></div>
        <div class="project-body"><h3>Lorem ipsum dolor sit amet</h3><p>Lorem ipsum dolor sit amet, consectetuer adipiscing elit. Sed diam nonummy nibh euismod tincidunt.</p><div class="bar"><span style="width:8%"></span></div><div class="funded">8% funded</div></div>
        <div class="project-btn">See Project Details</div>
      </article>
      <article class="project">
        <div class="project-photo p3" role="img" aria-label="Harbour skyline at night"><span class="price">From GBP 750</span></div>
        <div class="project-body"><h3>Lorem ipsum dolor sit amet</h3><p>Lorem ipsum dolor sit amet, consectetuer adipiscing elit. Sed diam nonummy nibh euismod tincidunt.</p><div class="bar"><span style="width:51%"></span></div><div class="funded">51% funded</div></div>
        <div class="project-btn">See Project Details</div>
      </article>
    </div>
  </section>

  <section class="press">
    <h4>FEATURED IN</h4>
    <div class="press-row"><span class="badge" style="width:80px"></span><span class="badge" style="width:90px"></span><span class="badge" style="width:96px"></span><span class="badge" style="width:70px"></span><span class="badge" style="width:30px"></span><span class="badge" style="width:100px"></span></div>
    <div class="press-row"><span class="badge" style="width:90px"></span><span class="badge" style="width:260px"></span></div>
  </section>

  <section class="community">
    <h2>Be Part of Growing International Community</h2>
    <p class="lead">Gain access to new products in world class cities and join our growing our community international landlords</p>
    <ul><li>A community of international property barons</li><li>Collective buying power at the pennyduke community</li><li>Attractive real estate from around the world</li></ul>
  </section>

  <section class="legal">
    <p>By accessing this website and any pages thereof, you agree to be bound by the terms and conditions. This website is only suitable, intended and available for professional or sophisticated, or similar investor in other jurisdictions, or those who are members of the pennyduke community and familiar with, and willing to accept the risks associated with private participations. pennyduke does not endorse any of the projects that appear on this website, nor does it make any recommendation the appropriateness of particular opportunities for any participant. Each potential participant must review and evaluate the projects in his or her own discretion and determine the suitability of participating.</p>
    <p>This website is every respect unaffiliated with any site to which links or to any company or entity (and connected projects). Investment opportunity or site featured on this site, and do not ensure as an endorsement of any of those companies or entities ("third parties"). Furthermore and for avoidance of doubt, pennyduke Limited is in no way affiliated with any third parties featured or reflected on these sits. There is no commercial relationship between pennyduke Limited and such third parties, nor an agency arrangement or similar. If you believe your content (including third party content) as such forms is defined in our Terms of Services has been reproduced on this site without permission, please refer to our Terms of service for information on how to request its removal from the site.</p>
  </section>
</div>

<footer class="site-footer">
  <nav class="foot-nav"><span>Terms of Service</span><span>Privacy Policy</span><span>How it Works</span><span>Discover A Project</span><span>Our Blog</span><span>FAQ</span><span>Contact Us</span></nav>
  <div class="follow">FOLLOW US ON <i></i><i></i><i></i><i></i><i></i><i></i></div>
  <p class="copyright">Copyright © 2014, pennyduke.com, all rights reserved.</p>
</footer>
</body>
</html>
```